PostCard Design Project

I am making a mailing postcard
I am having the mailing printed using 4 color foil on certain parts.
I am looking for a design that maximizes the foil process where certain parts are done in foil to grab the customers attention (example: if there is a car on the postcard the headlights would be done in foil) .
I am targeting some industries, (auto, real estate, medical, beauty) I would like the post card to have examples of postcard ideas for 2 or 3 of these industries.
specs:
the postcard should be atleast 6.5x9 up to 8.5x11, I don't want to restrict the space for the creative as I don't want everything to look like a huge mess. both sides will be used.
the piece is a direct mail piece so it has to meet requirements of https://www.mailvantor.com/business/pdf/quick-reference-guide.pdf
text will be
"business with no limits, meet mailing with no addresses, gain new customers through "Open Porch Route Drop" reach new customers at their home without needing their address. "
I also want some current print specials I am running included.
-double your order FREE (order 500 business cards and get 1000)
-250 100lb gloss stock brochures 99.00
-business packages (cards, envelopes and letterhead) 299
-1000 flyers 140.40
-5000 postcards 179.99
A list of services
banners
booklets
brochures
business cards
calendars
catalogs
CD/DVD packages
envelopes
event tickets
flyers
hangtags
postcards
posters
presentation folders
rack cards
labels
table tents
window cling and decal
"order 24/7 orders@inkwillow.com" must be included
my logo is InkWillow will be supplied later
ive received some great designs. however Im looking for something a little more modern like some zorvel would put out. if the amount of words is too much please feel free to edit. also an idea i had for the list of services i offer is to have it transparent yet readable as the background of the postcard some small some big but covering the entire backgroud. you can then design on top of that with other thing. just an early morning thought
Reason: I have uploaded a sketch of my idea, please take time to look at it for an accurate depiction of what im looking for. feel free to add elements that make it pop off the page
Reason: We are getting close i will be providing feed back today

```html
<!DOCTYPE html>
<html lang="en">
<head>
<meta charset="utf-8">
<title>InkWillow Postcard</title>
<link rel="stylesheet" href="https://fonts.googleapis.com/css2?family=Archivo+Black&family=Open+Sans:wght@400;600;700&family=Arimo:wght@700&display=swap">
<style>
  :root {
    --page: #e9e6e1;
    --card: #0d0d0d;
    --card-edge: #1c1c1c;
    --band-top: #3a3a3a;
    --band-bottom: #1a1a1a;
    --yellow: #e8e21f;
    --cyan: #2bb6e3;
    --lime: #b9d62c;
    --white: #ffffff;
    --ghost: #4a4a4a;
    --ghost-soft: #333333;
    --ring: #c8dc2a;
  }
  * { box-sizing: border-box; margin: 0; padding: 0; }
  html, body { width: 1200px; height: 900px; overflow: hidden; }
  body { background: var(--page); position: relative; font-family: "Open Sans", sans-serif; }

  .postcard {
    position: absolute; top: 250px; width: 570px; height: 380px;
    background: var(--card); overflow: hidden;
    box-shadow: 0 10px 30px rgba(0,0,0,.25);
  }
  .postcard--front { left: 20px; }
  .postcard--back { left: 610px; }

  .base-band {
    position: absolute; left: 0; right: 0; bottom: 0; height: 38px;
    background: linear-gradient(var(--band-top), var(--band-bottom));
  }
  .brand-mark {
    position: absolute; bottom: 7px;
    font-family: "Arimo", sans-serif; font-weight: 700; font-size: 21px;
    color: var(--yellow); white-space: nowrap;
  }
  .postcard--front .brand-mark { right: 18px; }
  .postcard--back .brand-mark { left: 18px; z-index: 3; }

  /* front */
  .headline {
    position: absolute; left: 20px; top: 150px;
    font-family: "Archivo Black", sans-serif; font-size: 27px; line-height: 29px;
    color: var(--yellow); text-transform: uppercase;
  }
  .sample-gallery { position: absolute; inset: 0; }
  .sample {
    position: absolute; border: 1px solid #2a2a2a;
  }
  .sample--beauty { left: 300px; top: 12px; width: 150px; height: 88px;
    background: linear-gradient(135deg, #f4f1ec 0%, #e2cdbb 60%, #c9a58c 100%); }
  .sample--jewelry { left: 360px; top: 50px; width: 195px; height: 120px;
    background: radial-gradient(circle at 60% 45%, #8c8c8c 0%, #3a3a3a 55%, #151515 100%); }
  .sample--auto { left: 195px; top: 80px; width: 160px; height: 118px;
    background: linear-gradient(160deg, #4d5257 0%, #1f2326 55%, #0b0c0d 100%); }
  .sample--bridal { left: 330px; top: 140px; width: 140px; height: 82px;
    background: linear-gradient(135deg, #ffffff 0%, #ececec 60%, #d4d4d4 100%); }

  .order-line {
    position: absolute; left: 200px; top: 214px;
    font-weight: 700; color: var(--yellow); font-size: 15px; line-height: 17px;
  }
  .specials {
    position: absolute; left: 200px; top: 254px; list-style: none;
    color: var(--white); font-size: 10.5px; line-height: 15px;
  }
  .specials li::before { content: "\2714"; margin-right: 6px; font-size: 9px; }

  /* back */
  .service-field {
    position: absolute; left: -20px; top: 4px; right: 0;
    font-weight: 600; font-size: 15px; line-height: 24px;
    color: var(--ghost); white-space: nowrap;
  }
  .service-row { display: block; }
  .service-row .dot { color: var(--ghost-soft); margin: 0 4px; }
  .hl-yellow { color: var(--yellow); }
  .hl-cyan { color: var(--cyan); }
  .hl-lime { color: var(--lime); }

  .postage-box {
    position: absolute; right: 16px; top: 14px; width: 74px; height: 48px;
    background: var(--white); z-index: 3;
    display: flex; align-items: center; justify-content: center; text-align: center;
    font-size: 9px; line-height: 11px; color: #222;
  }
  .showcase { position: absolute; width: 96px; height: 96px; border-radius: 50%;
    background: var(--white); border: 5px solid var(--ring); z-index: 3;
    display: flex; align-items: center; justify-content: center; }
  .showcase span { width: 72px; height: 72px; border-radius: 50%; display: block; }
  .showcase--folder { left: 330px; top: 40px; }
  .showcase--folder span { background: linear-gradient(135deg, #e6f0f2, #8fc0c7); }
  .showcase--media { left: 450px; top: 86px; }
  .showcase--media span { background: linear-gradient(135deg, #f5c33a, #3a8fd6 55%, #d8e2ec); }
  .showcase--flyer { left: 360px; top: 160px; }
  .showcase--flyer span { background: linear-gradient(135deg, #f1e3f0, #b0417f 55%, #e9e9f2); }
</style>
</head>
<body>

<section class="postcard postcard--front" aria-label="Postcard front">
  <div class="sample-gallery">
    <div class="sample sample--auto" role="img" aria-label="Sample auto detailing postcard with a car"></div>
    <div class="sample sample--beauty" role="img" aria-label="Sample dental beauty postcard"></div>
    <div class="sample sample--jewelry" role="img" aria-label="Sample jewelry postcard with rings"></div>
    <div class="sample sample--bridal" role="img" aria-label="Sample save the date card with a ring"></div>
  </div>
  <h1 class="headline">Let us<br>make<br>your<br>buissness<br>shine !</h1>
  <p class="order-line">24 hr/7 Day<br>orders@inkwillow.com</p>
  <ul class="specials">
    <li>Double your order FREE (order 500 business cards and get 1000)</li>
    <li>250 100lb gloss stock brochures 99.00</li>
    <li>Business packages (cards, envelopes and letterhead) 299</li>
    <li>1000 flyers 140.40</li>
    <li>5000 postcards 179.99</li>
  </ul>
  <div class="base-band"></div>
  <div class="brand-mark">InkWillow Logo</div>
</section>

<section class="postcard postcard--back" aria-label="Postcard back">
  <div class="service-field">
    <span class="service-row">business cards<span class="dot">•</span>CD/DVD packages<span class="dot">•</span>brochures<span class="dot">•</span>business cards<span class="dot">•</span>banners</span>
    <span class="service-row">banners<span class="dot">•</span>booklets<span class="dot">•</span>brochures<span class="dot">•</span>event tickets<span class="dot">•</span>CD/DVD packages</span>
    <span class="service-row">brochures<span class="dot">•</span>banners<span class="dot">•</span>calendars<span class="dot">•</span>envelopes<span class="dot">•</span>hangtags</span>
    <span class="service-row">booklets<span class="dot">•</span><span class="hl-yellow">banners</span><span class="dot">•</span>catalogs<span class="dot">•</span>event tickets<span class="dot">•</span>postcards</span>
    <span class="service-row">brochures<span class="dot">•</span><span class="hl-cyan">booklets</span><span class="dot">•</span>brochures<span class="dot">•</span>calendars<span class="dot">•</span>posters</span>
    <span class="service-row">business cards<span class="dot">•</span><span class="hl-lime">brochures</span><span class="dot">•</span><span class="hl-cyan">business cards</span><span class="dot">•</span>catalogs</span>
    <span class="service-row">calendars<span class="dot">•</span><span class="hl-yellow">calendars</span><span class="dot">•</span><span class="hl-lime">CD/DVD packages</span><span class="dot">•</span>envelopes</span>
    <span class="service-row">catalogs<span class="dot">•</span><span class="hl-cyan">catalogs</span><span class="dot">•</span><span class="hl-cyan">envelopes</span><span class="dot">•</span><span class="hl-yellow">event tickets</span><span class="dot">•</span>flyers</span>
    <span class="service-row">CD/DVD packages<span class="dot">•</span><span class="hl-cyan">flyers</span><span class="dot">•</span><span class="hl-lime">hangtags</span><span class="dot">•</span><span class="hl-cyan">presentation folders</span></span>
    <span class="service-row">envelopes<span class="dot">•</span>event tickets<span class="dot">•</span><span class="hl-cyan">postcards</span><span class="dot">•</span><span class="hl-yellow">rack cards</span><span class="dot">•</span>table tents</span>
    <span class="service-row">flyers<span class="dot">•</span>hangtags<span class="dot">•</span><span class="hl-lime">posters</span><span class="dot">•</span><span class="hl-cyan">labels</span><span class="dot">•</span><span class="hl-cyan">window cling and decal</span></span>
    <span class="service-row">postcards<span class="dot">•</span>posters<span class="dot">•</span>presentation folders<span class="dot">•</span><span class="hl-yellow">table tents</span><span class="dot">•</span>labels</span>
    <span class="service-row">rack cards<span class="dot">•</span>labels<span class="dot">•</span>table tents<span class="dot">•</span>window cling and decal</span>
    <span class="service-row">table tents<span class="dot">•</span>window cling and decal<span class="dot">•</span>rack cards<span class="dot">•</span>labels</span>
    <span class="service-row">window cling and decal<span class="dot">•</span>table tents<span class="dot">•</span>banners<span class="dot">•</span>booklets</span>
  </div>
  <div class="postage-box">Postage<br>Stamp</div>
  <div class="showcase showcase--folder"><span role="img" aria-label="Presentation folder sample"></span></div>
  <div class="showcase showcase--media"><span role="img" aria-label="CD and DVD package samples"></span></div>
  <div class="showcase showcase--flyer"><span role="img" aria-label="Flyer sample"></span></div>
  <div class="base-band"></div>
  <div class="brand-mark">InkWillow Logo</div>
</section>

</body>
</html>
```